uk based ecommerce website requires fresh look ,high quality look and feel

we are a web based company selling eco friendly ground reinforcement grids to diy and construction sectors
our existing website is www.pondermeshpaths.co.uk ,

we have already updated the logo so that is the branding sorted .so we need a ecommerce website that is very much up-to date in design and layout and which has content management system for ease of use so that we can add products and information as required.

Use current logo as reference for colour scheme.
www.pondermeshpaths.co.uk

The current website has 6 pages accessible through the navigation bar, I would now like 5 pages, removing the need for the Trade Enquiries page possibly have it with along with contact us.

Target Market(s)

construction industry , diy end users,
retail market, landscapers, gardeners

Industry/Entity Type

Construction

Font styles to use
Other font styles liked:
• logo font prometo

Colors
f78f20
9bcb3c

Requirements
Must have
• logo colours and logo design in website with cms responsive design for tablet and mobile devices
• expect content to work flawlessly and look great across all devices
• HTML 5 custom design with coding as required
• must have good experiance in ecommerce website design
• eye catching, high quality look and feel and very user friedly ,very up-to date.
Nice to have
• picture slider show
• explain in writing what exactly i am getting in my ecommerce website
Should not have
• plain , basic design , old fashion looking ,cheap look

```html
<!DOCTYPE html>
<html lang="en">
<head>
<meta charset="utf-8">
<title>PonderMesh Ground Solutions</title>
<link href="https://fonts.googleapis.com/css2?family=Open+Sans:wght@400;600;700&family=Montserrat:wght@600;700&display=swap" rel="stylesheet">
<style>
:root{
  --orange:#f78f20;
  --orange-dark:#ea7d12;
  --green:#9bcb3c;
  --green-dark:#7fb12a;
  --charcoal:#2c2c2c;
  --text:#444;
  --muted:#777;
  --line:#e2e2e2;
  --page:#f5f5f5;
  --white:#fff;
}
*{box-sizing:border-box;margin:0;padding:0}
html,body{width:835px;height:1200px;overflow:hidden}
body{position:relative;background:var(--page);font-family:"Open Sans",Arial,sans-serif;color:var(--text)}
.topline{position:absolute;left:0;top:0;width:835px;height:2px;background:var(--green)}
.header{position:absolute;left:0;top:2px;width:835px;height:74px;background:var(--white)}
.logo{position:absolute;left:68px;top:24px;display:flex;align-items:center;gap:8px}
.logo-mark{width:36px;height:36px;border-radius:50%;background:var(--green)}
.logo-name{font-family:"Open Sans",sans-serif;font-weight:700;font-size:15px;line-height:15px;color:var(--orange)}
.logo-tag{font-family:"Open Sans",sans-serif;font-weight:700;font-size:15px;line-height:15px;color:var(--orange);display:none}
.toplinks{position:absolute;left:540px;top:21px;font-size:6.5px;color:#666;letter-spacing:.2px;word-spacing:2px}
.toplinks span{margin:0 9px}
.search{position:absolute;left:494px;top:45px;width:160px;height:16px;border:1px solid var(--line);font-size:6px;color:#999;padding:4px 6px}
.search b{position:absolute;right:2px;top:2px;height:10px;width:38px;background:var(--green);color:#fff;font-weight:400;font-size:6px;text-align:center;line-height:10px}
.cart{position:absolute;left:666px;top:45px;width:100px;height:16px;border:1px solid var(--line);font-size:6px;color:#555;padding:4px 0 0 20px}
.cart svg{position:absolute;left:8px;top:4px}
.cart em{font-style:normal;color:var(--orange)}
.nav{position:absolute;left:68px;top:86px;width:698px;height:33px;background:var(--orange);display:flex;font-size:7.5px;color:#fff}
.nav .products{width:143px;background:var(--green);font-family:"Montserrat",sans-serif;font-weight:600;font-size:9.5px;line-height:33px;padding-left:36px;letter-spacing:.3px}
.nav .products i{font-style:normal;margin-left:18px;font-size:7px}
.nav a{line-height:33px;padding:0 20px;border-right:1px solid rgba(0,0,0,.08);color:#fff;text-decoration:none}
.sidebar{position:absolute;left:68px;top:130px;width:142px;background:var(--white);border:1px solid var(--line)}
.sidebar li{list-style:none;height:28.7px;line-height:28.7px;padding-left:11px;font-size:6.8px;color:#666;border-bottom:1px solid var(--line)}
.sidebar li:last-child{border-bottom:0}
.slider{position:absolute;left:224px;top:130px;width:542px;height:292px;background:linear-gradient(135deg,#5f8c3a 0%,#4c7a30 40%,#8e8a82 55%,#5a8936 70%,#7a5a44 100%)}
.slider h1{position:absolute;left:23px;top:96px;font-family:"Montserrat",sans-serif;font-weight:700;font-size:20px;color:#fff;letter-spacing:1px}
.slider h2{position:absolute;left:25px;top:127px;font-size:9px;font-weight:700;color:#fff;letter-spacing:.4px}
.slider p{position:absolute;left:26px;top:143px;width:210px;font-size:7.2px;line-height:14.5px;color:#fff}
.btn{display:inline-block;background:var(--green);color:#fff;font-weight:700;font-size:7px;text-align:center;border-radius:2px;border-bottom:2px solid var(--green-dark)}
.slider .btn{position:absolute;left:26px;top:182px;width:97px;height:30px;line-height:29px;font-size:8px}
.slider-arrows{position:absolute;right:22px;top:234px;display:flex;gap:1px}
.slider-arrows span{width:18px;height:18px;background:var(--orange);display:flex;align-items:center;justify-content:center}
.bar{position:absolute;top:439px;height:32px;background:var(--charcoal);color:#fff;font-family:"Montserrat",sans-serif;font-weight:600;font-size:10.5px;letter-spacing:.4px}
.bar .title{position:absolute;left:8px;top:0;line-height:32px}
.bar .arrows{position:absolute;right:8px;top:11px}
.special{left:69px;width:174px}
.featured{left:259px;width:507px}
.featured .tag{position:absolute;left:0;top:0;width:151px;height:32px;background:var(--orange);padding-left:12px;line-height:32px}
.sort{position:absolute;left:324px;top:12px;font-family:"Open Sans",sans-serif;font-size:6.5px;font-weight:700}
.sort-select{position:absolute;left:370px;top:0;top:-1px;top:0px}
.select{position:absolute;left:370px;top:6px;width:105px;height:20px;border:1px solid #555;font-family:"Open Sans",sans-serif;font-size:6px;font-weight:600;padding:6px 0 0 6px}
.select svg{position:absolute;right:6px;top:7px}
.card{position:absolute;width:160px;background:var(--white);border:1px solid var(--line);text-align:center}
.card .photo{margin:9px 8px 0;height:115px}
.card h3{margin-top:16px;font-size:9.5px;font-weight:700;color:#333;letter-spacing:.2px}
.card .price{font-size:9.5px;font-weight:700;color:#333;margin-top:3px}
.card .more{font-size:7.6px;color:#555;margin-top:3px}
.stars{color:var(--orange);font-size:8px;letter-spacing:1px}
.stars small{color:#444;font-size:6.5px;letter-spacing:0;margin-left:2px}
.card .stars{margin-top:4px}
.card .btn{margin-top:11px;width:77px;height:26px;line-height:25px}
.newbar{left:69px;top:746px;width:174px}
.newpanel{position:absolute;left:69px;top:786px;width:174px;height:201px;background:var(--white);border:1px solid var(--line)}
.newitem{position:absolute;left:14px;width:150px;height:70px}
.newitem .thumb{position:absolute;left:0;top:8px;width:52px;height:52px}
.newitem .badge{position:absolute;left:-8px;top:0;width:26px;height:26px;border-radius:50%;background:var(--orange);color:#fff;font-size:6.5px;font-weight:700;line-height:26px;text-align:center;transform:rotate(-20px)}
.newitem h4{position:absolute;left:66px;top:10px;font-size:9.5px;font-weight:700;color:#333}
.newitem .stars{position:absolute;left:66px;top:25px}
.newitem .count{position:absolute;left:66px;top:40px;font-size:6.5px;color:#444}
.newitem .link{position:absolute;left:66px;top:54px;font-size:6.5px;font-weight:700;color:var(--green);text-decoration:underline}
.newdivider{position:absolute;left:14px;top:99px;width:146px;height:1px;background:var(--line)}
.footer{position:absolute;left:0;top:1022px;width:835px;height:140px;background:linear-gradient(#f78f20,#f59a33)}
.fcol{position:absolute;top:26px;color:#fff}
.fcol h5{font-size:8.8px;font-weight:700;letter-spacing:.3px;margin-bottom:9px}
.fcol li{list-style:none;font-size:7.8px;line-height:16.8px}
.social{display:flex;gap:5px;margin-top:9px}
.social span{width:17px;height:17px;border:1.2px solid #fff;border-radius:50%}
.pay{display:flex;gap:4px;margin-top:13px}
.pay span{height:15px;padding:0 4px;background:#fff;color:#234;font-size:6.5px;font-weight:700;line-height:15px;border:1px solid #ddd}
.copy{position:absolute;left:0;top:1162px;width:835px;height:38px;background:var(--green);color:#fff;font-size:7.5px;text-align:center;line-height:38px}
.copy b{position:absolute;right:34px;top:0;font-weight:400}
</style>
</head>
<body>
<div class="topline"></div>
<header class="header">
  <div class="logo"><span class="logo-mark"></span><span class="logo-name">PONDERMESH</span></div>
  <div class="toplinks">HOME<span>|</span>MY ACCOUNT<span>|</span>LOGIN<span>|</span>REGISTER</div>
  <div class="search">SEARCH YOUR ITEMS :<b>SEARCH</b></div>
  <div class="cart"><svg width="8" height="7" viewBox="0 0 8 7"><path d="M0 0h1.5l1 4h4.5l1-3H2" fill="none" stroke="#f78f20" stroke-width="1"/><circle cx="3" cy="6" r=".8" fill="#f78f20"/><circle cx="6.5" cy="6" r=".8" fill="#f78f20"/></svg>YOUR CART IS : <em>0 ITEMS</em></div>
</header>

<nav class="nav">
  <div class="products">PRODUCTS<i>&#8964;</i></div>
  <a>SHOP</a><a>ABOUT US</a><a>GROUND</a><a>SOLUTIONS</a><a>PONDERMESH</a><a style="border:0">CONTACT US</a>
</nav>

<ul class="sidebar">
  <li>GEOTEXTILE MEMBRANES</li><li>LIGHT DOMESTIC DRIVEWAYS</li><li>HEAVY DOMESTIC DRIVEWAYS</li><li>PARKING AND PATHWAY SYSTEM</li><li>GRASS REINFORCEMENT MESH &amp;</li><li>TURF REINFORCEMENT MESH</li><li>STEEL U PINS</li><li>COMMERCIAL PARKING SYSTEM</li><li>PADDOCK GRID</li><li>MONTHLY SPECIALS</li>
</ul>

<section class="slider" role="img" aria-label="Aerial view of a curving gravel path through a lawn beside timber decking">
  <h1>PONDERMESH ECO</h1>
  <h2>SOLUTIONS LTD STABILISED GRAVEL</h2>
  <p>Part of a natural porous paving system, when filled with gravel this gives you an eco-friendly</p>
  <span class="btn">VIEW PRODUCT</span>
  <div class="slider-arrows">
    <span><svg width="6" height="8"><path d="M5 1L1.5 4 5 7" fill="none" stroke="#fff" stroke-width="1.2"/></svg></span>
    <span><svg width="6" height="8"><path d="M1 1l3.5 3L1 7" fill="none" stroke="#fff" stroke-width="1.2"/></svg></span>
  </div>
</section>

<div class="bar special"><span class="title">SPECIAL PRODUCTS</span>
  <svg class="arrows" width="16" height="10"><path d="M4 1L1 5l3 4M12 1l3 4-3 4" fill="none" stroke="#fff" stroke-width="1.3"/></svg></div>
<div class="bar featured"><span class="tag">FEATURED PRODUCTS</span>
  <span class="sort">SORT BY :</span>
  <div class="select">PRICE: RS LOW TO HIGH<svg width="6" height="4"><path d="M.5.5l2.5 2.5L5.5.5" fill="none" stroke="#fff"/></svg></div>
  <svg class="arrows" width="16" height="10"><path d="M4 1L1 5l3 4M12 1l3 4-3 4" fill="none" stroke="#fff" stroke-width="1.3"/></svg></div>

<article class="card" style="left:69px;top:485px;width:174px;height:241px">
  <div class="photo" role="img" aria-label="Black geotextile membrane laid over ground beside a timber fence" style="background:linear-gradient(#8a8a7c,#3e4042 55%,#2f3133)"></div>
  <h3>GEOTEXTILE MEMBRANES</h3><div class="price">£ 44.99</div><div class="more">View Full Details</div>
  <div class="stars">★★★★☆<small>120 Reviews</small></div><span class="btn">ADD TO CART</span>
</article>
<article class="card" style="left:259px;top:485px;height:241px">
  <div class="photo" role="img" aria-label="White house with a gravel driveway" style="background:linear-gradient(#b7c6d3,#d9d9d4 45%,#6e8d4f 70%,#bdb8ad)"></div>
  <h3>DRIVEWAY MEMBRANE</h3><div class="price">£ 44.99</div><div class="more">View Full Details</div>
  <div class="stars">★★★★☆<small>120 Reviews</small></div><span class="btn">ADD TO CART</span>
</article>
<article class="card" style="left:433px;top:485px;height:241px">
  <div class="photo" role="img" aria-label="Wheel rolling over a gravel-filled grid" style="background:linear-gradient(135deg,#7a7a7a,#3a3a3a 60%,#8a8a8a)"></div>
  <h3>PONDERMESH 25 SYSTEM</h3><div class="price">£ 44.99</div><div class="more">View Full Details</div>
  <div class="stars">★★★★☆<small>120 Reviews</small></div><span class="btn">ADD TO CART</span>
</article>
<article class="card" style="left:606px;top:485px;height:241px">
  <div class="photo" role="img" aria-label="Truck tyre resting on a paving grid" style="background:linear-gradient(135deg,#5d5a55,#2a2a2a 55%,#b9ad98)"></div>
  <h3>TERRALOK 40 PAVING</h3><div class="price">£ 44.99</div><div class="more">View Full Details</div>
  <div class="stars">★★★★☆<small>120 Reviews</small></div><span class="btn">ADD TO CART</span>
</article>

<div class="bar newbar"><span class="title" style="left:10px">NEW PRODUCTS</span>
  <svg class="arrows" width="16" height="10"><path d="M4 1L1 5l3 4M12 1l3 4-3 4" fill="none" stroke="#fff" stroke-width="1.3"/></svg></div>
<aside class="newpanel">
  <div class="newitem" style="top:12px">
    <div class="thumb" role="img" aria-label="Gravel-filled grid sample" style="background:linear-gradient(135deg,#cfc9bd,#8f8677)"></div>
    <span class="badge">NEW</span>
    <h4>PONDERMESH 25</h4><div class="stars">★★★★☆</div><div class="count">120 Reviews</div><span class="link">VIEW FULL DETAILS</span>
  </div>
  <div class="newdivider"></div>
  <div class="newitem" style="top:103px">
    <div class="thumb" role="img" aria-label="Black gravel grid panel" style="background:linear-gradient(135deg,#666,#222)"></div>
    <span class="badge">NEW</span>
    <h4>GRAVEL GRID</h4><div class="stars">★★★★☆</div><div class="count">120 Reviews</div><span class="link">VIEW FULL DETAILS</span>
  </div>
</aside>

<article class="card" style="left:259px;top:746px;height:241px">
  <div class="photo" role="img" aria-label="Gravel poured into black hexagonal grid" style="background:linear-gradient(#c9c7c2,#8d8b87 40%,#2d2d2d)"></div>
  <h3>DRIVEWAY MEMBRANE</h3><div class="price">£ 44.99</div><div class="more">View Full Details</div>
  <div class="stars">★★★★☆<small>120 Reviews</small></div><span class="btn">ADD TO CART</span>
</article>
<article class="card" style="left:433px;top:746px;height:241px">
  <div class="photo" role="img" aria-label="Wheels on a white gravel grid" style="background:linear-gradient(135deg,#a39a8c,#6e6a64 45%,#e4e6e8)"></div>
  <h3>PONDERMESH 25 SYSTEM</h3><div class="price">£ 44.99</div><div class="more">View Full Details</div>
  <div class="stars">★★★★☆<small>120 Reviews</small></div><span class="btn">ADD TO CART</span>
</article>
<article class="card" style="left:606px;top:746px;height:241px">
  <div class="photo" role="img" aria-label="Black paving grid laid beside planting" style="background:linear-gradient(135deg,#5a4a3a,#1f1f1f 50%,#a9a9a9)"></div>
  <h3>TERRALOK 40 PAVING</h3><div class="price">£ 44.99</div><div class="more">View Full Details</div>
  <div class="stars">★★★★☆<small>120 Reviews</small></div><span class="btn">ADD TO CART</span>
</article>

<footer class="footer">
  <div class="fcol" style="left:68px"><h5>INFORMATION</h5><ul><li>About Us</li><li>Delivery Information</li><li>Privacy Policy</li><li>Terms &amp; Conditions</li></ul></div>
  <div class="fcol" style="left:211px"><h5>CUSTOMER SERVICE</h5><ul><li>Contact Us</li><li>Returns</li><li>Site Map</li><li>FAQ's</li></ul></div>
  <div class="fcol" style="left:354px"><h5>EXTRAS</h5><ul><li>Brands</li><li>Gift Vouchers</li><li>Affiliates</li><li>Specials</li></ul></div>
  <div class="fcol" style="left:468px"><h5>MY ACCOUNT</h5><ul><li>My Account</li><li>Order History</li><li>Wish List</li><li>Newsletter</li></ul></div>
  <div class="fcol" style="left:587px"><h5>FOLLOW US</h5><ul><li>Connect with our social network</li></ul>
    <div class="social"><span></span><span></span><span></span><span></span><span></span></div>
    <div class="pay"><span>PayNest</span><span>CARDA</span><span>AMVO</span><span>MERI</span></div>
  </div>
</footer>
<div class="copy">©2016. PONDERMESHPATHS. ALL RIGHTS RESERVED.<b>C22</b></div>
</body>
</html>
```